Web Developer Needs a Business Card Design

I need a personal business card design that represents me as a web developer for potential employers. I would like the background to be a dark color on the front for contrast with my logo and name. The back will have all my information along with a smaller version of the logo. I want something with a modern look and feel, not too conservative. This will be used for potential employers and freelance work.

Industry/Entity Type

Business

Contact Information for Business Card

Front should have my logo and name. The back should have all my personal information which would include: name: Tom Varulek, phone: 570-614-3098, email: tomvarulek@quillbox.net, website url: www.tomvarulek.net, logo, web developer.

Font styles to use
Sans Serif

Requirements
Must have
• Must include my logo. The color palette base color will be the logo color.

```html
<!DOCTYPE html>
<html lang="en">
<head>
<meta charset="utf-8">
<title>Tom Varulek – Business Card</title>
<link href="https://fonts.googleapis.com/css2?family=Open+Sans:wght@400;600&display=swap" rel="stylesheet">
<style>
  :root {
    --teal: #6cc8b5;
    --teal-light: #80d1c1;
    --ink: #111111;
    --paper: #ffffff;
    --backdrop: #e6e8e7;
  }
  * { box-sizing: border-box; margin: 0; padding: 0; }
  html, body { width: 1200px; height: 892px; overflow: hidden; }
  body {
    background: var(--backdrop);
    font-family: "Open Sans", Arial, sans-serif;
    color: var(--ink);
    position: relative;
  }
  .card {
    position: absolute;
    width: 540px;
    height: 309px;
    background: var(--paper);
    box-shadow: 0 6px 18px rgba(0,0,0,.15);
    overflow: hidden;
  }
  .card--info { left: 40px; top: 292px; }
  .card--front { left: 620px; top: 292px; }
  .card__shapes { position: absolute; inset: 0; }

  .logo-ring {
    position: absolute;
    border: 9px solid var(--teal);
    border-radius: 50%;
    display: flex; align-items: center; justify-content: center;
  }
  .logo-ring__name {
    font-weight: 600;
    font-size: 21px;
    color: var(--teal);
  }
  .card--info .logo-ring { left: 176px; top: 12px; width: 136px; height: 136px; }
  .card--front .logo-ring { left: 198px; top: 50px; width: 144px; height: 144px; }

  .identity { position: absolute; left: 36px; top: 146px; }
  .identity__name { font-size: 30px; font-weight: 400; line-height: 1; }
  .identity__role { font-size: 18px; line-height: 1.1; margin-top: 2px; }

  .divider {
    position: absolute; left: 192px; top: 202px;
    width: 2px; height: 70px; background: var(--ink);
  }
  .contact { position: absolute; left: 204px; top: 206px; list-style: none; }
  .contact__item {
    display: flex; align-items: center; gap: 5px;
    font-size: 15px; line-height: 21px;
  }
  .contact__icon { width: 12px; height: 12px; flex: none; }

  .front-name {
    position: absolute; left: 0; right: 0; top: 210px;
    text-align: center; font-size: 34px; font-weight: 600;
  }
</style>
</head>
<body>

<section class="card card--info" aria-label="Business card, contact side">
  <svg class="card__shapes" viewBox="0 0 540 309" width="540" height="309" aria-hidden="true">
    <path d="M294 0 C 424 45, 474 175, 474 309 L540 309 L540 0 Z" fill="var(--teal-light)"/>
    <path d="M290 0 C 420 45, 470 175, 470 309" fill="none" stroke="var(--ink)" stroke-width="5"/>
    <polygon points="0,202 172,202 194,309 0,309" fill="var(--teal)"/>
  </svg>

  <div class="logo-ring"><span class="logo-ring__name">varulek</span></div>

  <div class="identity">
    <h1 class="identity__name">Tom Varulek</h1>
    <p class="identity__role">web developer</p>
  </div>

  <div class="divider"></div>

  <ul class="contact">
    <li class="contact__item">
      <svg class="contact__icon" viewBox="0 0 12 12" aria-hidden="true"><rect width="12" height="12" rx="2" fill="var(--ink)"/><path d="M3.5 2.5 L5 4.5 L4.2 5.5 Q5 7.2 6.6 7.9 L7.5 7 L9.5 8.5 L8.6 9.6 Q5 9.5 2.6 4 Z" fill="#fff"/></svg>
      570-614-3098
    </li>
    <li class="contact__item">
      <svg class="contact__icon" viewBox="0 0 12 12" aria-hidden="true"><rect width="12" height="12" rx="2" fill="var(--ink)"/><rect x="2.5" y="3.5" width="7" height="5" fill="none" stroke="#fff" stroke-width="1"/><path d="M2.5 3.5 L6 6.5 L9.5 3.5" fill="none" stroke="#fff" stroke-width="1"/></svg>
      tomvarulek@quillbox.net
    </li>
    <li class="contact__item">
      <svg class="contact__icon" viewBox="0 0 12 12" aria-hidden="true"><rect width="12" height="12" rx="2" fill="var(--ink)"/><circle cx="6" cy="6" r="3.6" fill="none" stroke="#fff" stroke-width="1"/><path d="M2.4 6 H9.6 M6 2.4 Q4 6 6 9.6 M6 2.4 Q8 6 6 9.6" fill="none" stroke="#fff" stroke-width=".8"/></svg>
      www.tomvarulek.net
    </li>
  </ul>
</section>

<section class="card card--front" aria-label="Business card, front side">
  <div class="logo-ring"><span class="logo-ring__name">varulek</span></div>
  <h2 class="front-name">Tom Varulek</h2>
</section>

</body>
</html>
```